UI/ UX Design for ERP Software

We need a new UX/UI interface for a ERP software for property managers. Our CMMS / ERP solution is made based on responsive design technologies and is coded in PHP.
The overall UX to be similar to Tev Ulna - easy navigation, intuitive menus.

Industry/Entity Type

Property Management

Number of Pages Required

5+ page

Requirements
Must have
• Round dock buttons
Consistent icons across the application
Enough Spacing between buttons/icons/ menu
Consistent Font
Nice to have
• We would like the UX to allow the users to use the application without /minimum training.
Should not have
• we don't want anything that is classic with respect to UX

```html
<!DOCTYPE html>
<html lang="en">
<head>
<meta charset="utf-8">
<title>Estaro – Property ERP</title>
<link href="https://fonts.googleapis.com/css2?family=Inter:wght@400;500;600;700&display=swap" rel="stylesheet">
<style>
  :root{
    --ink:#1a1f2b;
    --muted:#4a6b94;
    --brand:#1e8fff;
    --page-top:#ffffff;
    --page-bottom:#f0f5fa;
    --win:#f6f9fd;
    --panel:#eaf1f8;
    --tile:#ffffff;
    --tab:#dde9f6;
    --orange:#ff7a1f;
    --sun:#ffb800;
  }
  *{box-sizing:border-box;margin:0;padding:0}
  html,body{width:1200px;height:1200px;overflow:hidden}
  body{font-family:"Inter",sans-serif;color:var(--ink);
    background:linear-gradient(to bottom,var(--page-top) 0,var(--page-top) 327px,var(--page-bottom) 327px)}
  .canvas{position:relative;width:1200px;height:1200px}
  .window{position:absolute;left:207px;width:787px;border-radius:20px;
    background:linear-gradient(180deg,#ffffff 0%,var(--win) 40%,#f1f6fb 100%);
    box-shadow:0 6px 30px rgba(30,60,110,.06)}
  .window--nav{top:42px;height:475px}
  .window--property{top:549px;height:594px}
  .dots{position:absolute;left:24px;top:9px;display:flex;gap:5px}
  .dots span{width:6px;height:6px;border-radius:50%}
  .dots span:nth-child(1){background:#ffc53d}
  .dots span:nth-child(2){background:#ff4d4d}
  .dots span:nth-child(3){background:#34c759}
  .brand{position:absolute;left:25px;top:31px;display:flex;align-items:center;gap:4px;
    font-size:13px;font-weight:600;color:var(--brand)}
  .brand i{width:12px;height:12px;background:var(--brand);border-radius:3px;display:block}
  .theme-toggle{position:absolute;left:562px;top:31px;width:48px;height:19px;border-radius:10px;
    background:#fff;box-shadow:0 1px 4px rgba(0,0,0,.06);display:flex;align-items:center;justify-content:space-between;padding:0 5px}
  .theme-toggle .knob{width:12px;height:12px;border-radius:50%;border:2px solid var(--sun)}
  .welcome{position:absolute;left:624px;top:34px;font-size:9px}
  .welcome b{font-weight:600}
  .avatar{position:absolute;left:731px;top:25px;width:30px;height:30px;border-radius:50%;
    background:linear-gradient(135deg,#7a5a48,#3b2f2a)}
  .page-title{position:absolute;left:0;right:0;top:69px;text-align:center;font-size:13px;font-weight:600}
  .nav-panel{position:absolute;left:160px;top:91px;width:467px;height:294px;border-radius:12px;background:var(--panel);
    padding:19px 0 0 22px;display:grid;grid-template-columns:repeat(6,71px);grid-auto-rows:58px;row-gap:8px}
  .nav-item{display:flex;flex-direction:column;align-items:center}
  .nav-item .tile{width:46px;height:46px;border-radius:10px;background:var(--tile);display:flex;align-items:center;justify-content:center;
    box-shadow:0 2px 6px rgba(30,60,110,.05)}
  .nav-item svg{width:20px;height:20px;fill:var(--ink)}
  .nav-item span{margin-top:4px;font-size:7px;white-space:nowrap}
  .nav-item.start2{grid-column-start:2}
  .dock{position:absolute;left:331px;width:125px;height:49px;border-radius:12px;background:#fff;
    box-shadow:0 4px 14px rgba(30,60,110,.08);display:flex;justify-content:center;align-items:center;gap:27px}
  .window--nav .dock{top:407px}
  .window--property .dock{top:525px}
  .dock-btn{width:32px;height:32px;border-radius:9px;display:flex;align-items:center;justify-content:center}
  .dock-btn--home{background:linear-gradient(180deg,#27b0ff,#1273ff);box-shadow:0 4px 10px rgba(18,115,255,.35)}
  .dock-btn--apps{background:linear-gradient(180deg,#ff9440,#ff5f1f);box-shadow:0 4px 10px rgba(255,95,31,.35)}
  .dock-btn svg{width:18px;height:18px;fill:#fff}
  .property-title{position:absolute;left:28px;top:68px;display:flex;align-items:center;gap:9px;font-size:13px;font-weight:600}
  .back{width:13px;height:13px;border-radius:50%;background:var(--ink);display:flex;align-items:center;justify-content:center}
  .tabs{position:absolute;left:30px;top:101px;width:740px;display:flex;flex-wrap:wrap;gap:10px 6px}
  .tab{height:24px;border-radius:5px;background:var(--tab);font-size:7px;font-weight:500;display:flex;align-items:center;justify-content:center}
  .tab--active{background:var(--brand);color:#fff;font-weight:600}
  .info-card{position:absolute;left:29px;top:172px;width:455px;height:338px;border-radius:10px;background:#fff}
  .info-card h2{position:absolute;left:20px;top:15px;font-size:11px;font-weight:600}
  .edit-link{position:absolute;left:367px;top:16px;display:flex;align-items:center;gap:6px;font-size:7.5px;font-weight:600;text-decoration:underline}
  .fields{position:absolute;left:25px;top:48px;display:grid;grid-template-columns:153px 132px 140px;grid-auto-flow:column;grid-template-rows:repeat(11,25.8px)}
  .field{font-size:7px;line-height:10px}
  .field dd{color:var(--muted)}
  .photo{position:absolute;width:125px;height:83px;border-radius:6px}
  .photo--city{left:500px;top:175px;background:linear-gradient(180deg,#1d3c7a,#2b4f8f 50%,#5d4a3a)}
  .photo--pool{left:635px;top:175px;background:linear-gradient(180deg,#cfd8e6,#8b93a0 50%,#4aa6d6)}
  .photo--lounge{left:500px;top:269px;background:linear-gradient(135deg,#ece9e4,#c9c7c3 60%,#8a8783)}
  .photo--roof{left:635px;top:269px;background:linear-gradient(180deg,#4d85c9,#b6c7d9 55%,#5b5e60)}
</style>
</head>
<body>
<svg width="0" height="0" style="position:absolute" aria-hidden="true">
  <defs>
    <symbol id="i-customers" viewBox="0 0 24 24"><circle cx="12" cy="8" r="3"/><circle cx="5.5" cy="9" r="2.2"/><circle cx="18.5" cy="9" r="2.2"/><path d="M7 17c0-3 2.2-5 5-5s5 2 5 5z"/><path d="M1.5 16c0-2.3 1.7-4 4-4 1 0 1.8.3 2.4.8A6 6 0 0 0 6 16z"/><path d="M22.5 16c0-2.3-1.7-4-4-4-1 0-1.8.3-2.4.8A6 6 0 0 1 18 16z"/></symbol>
    <symbol id="i-building" viewBox="0 0 24 24"><path d="M5 2h14v20h-5v-4h-4v4H5zm3 3v2h2V5zm6 0v2h2V5zM8 9v2h2V9zm6 0v2h2V9zm-6 4v2h2v-2zm6 0v2h2v-2z"/></symbol>
    <symbol id="i-tenant" viewBox="0 0 24 24"><path d="M12 2a10 10 0 1 0 0 20 10 10 0 0 0 0-20zm0 4a3.5 3.5 0 1 1 0 7 3.5 3.5 0 0 1 0-7zm0 14a8 8 0 0 1-6-2.7c1.2-1.8 3.4-2.8 6-2.8s4.8 1 6 2.8A8 8 0 0 1 12 20z"/></symbol>
    <symbol id="i-contact" viewBox="0 0 24 24"><circle cx="12" cy="7" r="4.5"/><path d="M4 21c0-4.5 3.5-7.5 8-7.5s8 3 8 7.5z"/></symbol>
    <symbol id="i-gears" viewBox="0 0 24 24"><path d="M9 5l1.4.4.9-1.3 1.6 1-.5 1.5 1 1 1.5-.5 1 1.6-1.3.9.4 1.4-1.5.6-.2 1.5-1.9.2-.6-1.5H9.4L8.8 13l-1.9-.2-.2-1.5L5.2 10.7l.4-1.4-1.3-.9 1-1.6 1.5.5 1-1 -.5-1.5 1.6-1 .9 1.3zM10 7.5a2 2 0 1 0 0 4 2 2 0 0 0 0-4z"/><circle cx="18" cy="5" r="2.6"/><circle cx="18" cy="17" r="2.8"/><circle cx="18" cy="5" r="1" fill="#fff"/><circle cx="18" cy="17" r="1" fill="#fff"/></symbol>
    <symbol id="i-employees" viewBox="0 0 24 24"><circle cx="8.5" cy="8" r="3.5"/><circle cx="17" cy="8" r="3"/><path d="M1.5 19c0-3.8 3-6 7-6s7 2.2 7 6z"/><path d="M16.5 13c3.5 0 6 1.9 6 6h-5.3c0-2.4-.9-4.5-2.6-5.8.6-.1 1.2-.2 1.9-.2z"/></symbol>
    <symbol id="i-wrench" viewBox="0 0 24 24"><path d="M21 6.5l-3 3-2.5-1-1-2.5 3-3a5.5 5.5 0 0 0-6.8 7L3 17.7A2.3 2.3 0 0 0 6.3 21l7.7-7.7a5.5 5.5 0 0 0 7-6.8z"/></symbol>
    <symbol id="i-briefcase" viewBox="0 0 24 24"><path d="M9 3h6a2 2 0 0 1 2 2v1h4a1 1 0 0 1 1 1v5H2V7a1 1 0 0 1 1-1h4V5a2 2 0 0 1 2-2zm0 2v1h6V5zM2 13.5h8.5V15h3v-1.5H22V20a1 1 0 0 1-1 1H3a1 1 0 0 1-1-1z"/></symbol>
    <symbol id="i-dollar" viewBox="0 0 24 24"><path d="M11 1h2v2.3c2.4.3 4.2 1.8 4.5 4.2h-2.6c-.3-1.3-1.5-2-3-2-1.9 0-3 .9-3 2.1 0 1.3 1.3 1.8 3.4 2.3 3 .7 5.5 1.7 5.5 4.7 0 2.5-2 4.2-4.8 4.6V21h-2v-1.8c-2.7-.3-4.8-2-5-4.7h2.6c.3 1.5 1.6 2.4 3.5 2.4 2 0 3.2-.9 3.2-2.2 0-1.4-1.2-1.9-3.6-2.5C8.9 11.6 6.6 10.6 6.6 7.7c0-2.2 1.8-4 4.4-4.4z"/></symbol>
    <symbol id="i-search" viewBox="0 0 24 24"><path d="M10 2a8 8 0 0 1 6.4 12.8l5.4 5.4-1.8 1.8-5.4-5.4A8 8 0 1 1 10 2zm0 3a5 5 0 1 0 0 10 5 5 0 0 0 0-10z"/></symbol>
    <symbol id="i-warning" viewBox="0 0 24 24"><path d="M12 2L1 21h22zm-1.2 6h2.4l-.3 7h-1.8zM12 16.5a1.3 1.3 0 1 1 0 2.6 1.3 1.3 0 0 1 0-2.6z"/></symbol>
    <symbol id="i-clipboard" viewBox="0 0 24 24"><path d="M9 2h6v2h4a1 1 0 0 1 1 1v16a1 1 0 0 1-1 1H5a1 1 0 0 1-1-1V5a1 1 0 0 1 1-1h4zM7 8v2h2V8zm4 0v2h6V8zm-4 4v2h2v-2zm4 0v2h6v-2zm-4 4v2h2v-2zm4 0v2h6v-2z"/></symbol>
    <symbol id="i-note" viewBox="0 0 24 24"><path d="M3 3h18v12h-6v6H3zm14 14h4l-4 4z"/></symbol>
    <symbol id="i-budget" viewBox="0 0 24 24"><path d="M5 1h9l5 5v16a1 1 0 0 1-1 1H5a1 1 0 0 1-1-1V2a1 1 0 0 1 1-1zm8 1v5h5zm-1.8 7v1.3c-1.4.2-2.3 1.1-2.3 2.3 0 1.4 1.1 2 2.6 2.3 1 .2 1.4.5 1.4 1s-.5.9-1.3.9-1.4-.4-1.5-1H8.6c.1 1.4 1 2.3 2.6 2.5V21h1.5v-1.3c1.5-.2 2.4-1.1 2.4-2.4 0-1.4-1-2-2.7-2.4-1-.2-1.3-.5-1.3-.9s.4-.8 1.1-.8 1.2.3 1.3.9h1.4c-.1-1.3-1-2.1-2.3-2.3V9z"/></symbol>
    <symbol id="i-tasks" viewBox="0 0 24 24"><path d="M2 4.5l1.2-1.2L4.5 4.6 7.3 1.8 8.5 3 4.5 7zM2 11.5l1.2-1.2 1.3 1.3 2.8-2.8 1.2 1.2-4 4zM10 4h12v2H10zm0 7h12v2H10zm0 7h12v2H10zM5 16.5a2 2 0 1 1 0 4 2 2 0 0 1 0-4z"/></symbol>
    <symbol id="i-bulb" viewBox="0 0 24 24"><path d="M12 1a7 7 0 0 1 4 12.7V16H8v-2.3A7 7 0 0 1 12 1zM8.5 17.5h7V19h-7zm1 2.5h5a2.5 2.5 0 0 1-5 0z"/></symbol>
    <symbol id="i-copy" viewBox="0 0 24 24"><path d="M8 1h8l5 5v12a1 1 0 0 1-1 1H8a1 1 0 0 1-1-1V2a1 1 0 0 1 1-1zm7 1v5h5zM4 5h2v15h11v2H4a1 1 0 0 1-1-1V6a1 1 0 0 1 1-1z"/></symbol>
    <symbol id="i-chart" viewBox="0 0 24 24"><path d="M2 3h2v16h18v2H2zm4 9h2v5H6zm4-4h2v9h-2zm4 2h2v7h-2zm4-5h2v12h-2z"/></symbol>
    <symbol id="i-sliders" viewBox="0 0 24 24"><path d="M2 5h20v2H2zm0 6h20v2H2zm0 6h20v2H2z"/><rect x="14" y="3" width="3" height="6" rx="1"/><rect x="6" y="9" width="3" height="6" rx="1"/><rect x="11" y="15" width="3" height="6" rx="1"/></symbol>
    <symbol id="i-cog" viewBox="0 0 24 24"><path d="M10 1h4l.6 3 2.2 1.2 2.8-1.2 2 3.4-2.3 2 .1 2.6 2.2 2-2 3.5-2.8-1.1-2.3 1.3L14 23h-4l-.6-3-2.2-1.3-2.8 1.1-2-3.5 2.3-2V11.6L2.4 9.6l2-3.4 2.8 1.2L9.4 4zM12 8.5a3.5 3.5 0 1 0 0 7 3.5 3.5 0 0 0 0-7z"/></symbol>
    <symbol id="i-home" viewBox="0 0 24 24"><path d="M12 2l11 9.5-1.5 1.5L20 11.7V21h-5.5v-6h-5v6H4v-9.3L2.5 13 1 11.5z"/></symbol>
    <symbol id="i-grid" viewBox="0 0 24 24"><circle cx="5" cy="5" r="2"/><circle cx="12" cy="5" r="2"/><circle cx="19" cy="5" r="2"/><circle cx="5" cy="12" r="2"/><circle cx="12" cy="12" r="2"/><circle cx="19" cy="12" r="2"/><circle cx="5" cy="19" r="2"/><circle cx="12" cy="19" r="2"/><circle cx="19" cy="19" r="2"/></symbol>
    <symbol id="i-sun" viewBox="0 0 24 24"><circle cx="12" cy="12" r="5"/><path d="M11 0h2v4h-2zm0 20h2v4h-2zM0 11h4v2H0zm20 0h4v2h-4zM3.5 5l1.5-1.5 2.8 2.8-1.5 1.5zm12.7 12.7l1.5-1.5 2.8 2.8-1.5 1.5zM3.5 19l2.8-2.8 1.5 1.5L5 20.5zM16.2 6.3L19 3.5 20.5 5l-2.8 2.8z"/></symbol>
  </defs>
</svg>

<div class="canvas">

  <section class="window window--nav">
    <div class="dots"><span></span><span></span><span></span></div>
    <div class="brand"><i></i>Estaro</div>
    <div class="theme-toggle"><svg width="11" height="11" style="fill:var(--sun)"><use href="#i-sun"/></svg><span class="knob"></span></div>
    <p class="welcome">Welcome, <b>Dana Reyes</b></p>
    <div class="avatar" role="img" aria-label="User profile photo"></div>
    <h1 class="page-title">Start navigation</h1>

    <nav class="nav-panel">
      <div class="nav-item"><div class="tile"><svg><use href="#i-customers"/></svg></div><span>Customers</span></div>
      <div class="nav-item"><div class="tile"><svg><use href="#i-building"/></svg></div><span>Properties</span></div>
      <div class="nav-item"><div class="tile"><svg><use href="#i-tenant"/></svg></div><span>Tenants</span></div>
      <div class="nav-item"><div class="tile"><svg><use href="#i-contact"/></svg></div><span>Contacts</span></div>
      <div class="nav-item"><div class="tile"><svg><use href="#i-gears"/></svg></div><span>Contractors</span></div>
      <div class="nav-item"><div class="tile"><svg><use href="#i-employees"/></svg></div><span>Employees</span></div>
      <div class="nav-item"><div class="tile"><svg><use href="#i-wrench"/></svg></div><span>Maintenance</span></div>
      <div class="nav-item"><div class="tile"><svg><use href="#i-briefcase"/></svg></div><span>Works orders</span></div>
      <div class="nav-item"><div class="tile"><svg><use href="#i-dollar"/></svg></div><span>Purcharse orders</span></div>
      <div class="nav-item"><div class="tile"><svg><use href="#i-search"/></svg></div><span>Inspections</span></div>
      <div class="nav-item"><div class="tile"><svg><use href="#i-warning"/></svg></div><span>Risk management</span></div>
      <div class="nav-item"><div class="tile"><svg><use href="#i-clipboard"/></svg></div><span>Compliance</span></div>
      <div class="nav-item start2"><div class="tile"><svg><use href="#i-note"/></svg></div><span>Tenant requests</span></div>
      <div class="nav-item"><div class="tile"><svg><use href="#i-budget"/></svg></div><span>Budgeting</span></div>
      <div class="nav-item"><div class="tile"><svg><use href="#i-tasks"/></svg></div><span>Project mngmt</span></div>
      <div class="nav-item"><div class="tile"><svg><use href="#i-bulb"/></svg></div><span>Energy</span></div>
      <div class="nav-item start2"><div class="tile"><svg><use href="#i-copy"/></svg></div><span>Reports</span></div>
      <div class="nav-item"><div class="tile"><svg><use href="#i-chart"/></svg></div><span>Analytics</span></div>
      <div class="nav-item"><div class="tile"><svg><use href="#i-sliders"/></svg></div><span>Configuration</span></div>
      <div class="nav-item"><div class="tile"><svg><use href="#i-cog"/></svg></div><span>Settings</span></div>
    </nav>

    <div class="dock">
      <div class="dock-btn dock-btn--home"><svg><use href="#i-home"/></svg></div>
      <div class="dock-btn dock-btn--apps"><svg><use href="#i-grid"/></svg></div>
    </div>
  </section>

  <section class="window window--property">
    <div class="dots"><span></span><span></span><span></span></div>
    <div class="brand"><i></i>Estaro</div>
    <div class="theme-toggle"><svg width="11" height="11" style="fill:var(--sun)"><use href="#i-sun"/></svg><span class="knob"></span></div>
    <p class="welcome">Welcome, <b>Dana Reyes</b></p>
    <div class="avatar" role="img" aria-label="User profile photo"></div>

    <h1 class="property-title"><span class="back"><svg width="7" height="7" viewBox="0 0 10 10"><path d="M6.5 1.5L3 5l3.5 3.5" stroke="#fff" stroke-width="1.8" fill="none"/></svg></span>Crest Tower</h1>

    <div class="tabs">
      <div class="tab tab--active" style="width:98px">General information</div>
      <div class="tab" style="width:93px">Organization chart</div>
      <div class="tab" style="width:73px">Tenant List</div>
      <div class="tab" style="width:82px">Property Assets</div>
      <div class="tab" style="width:82px">Contractor list</div>
      <div class="tab" style="width:99px">Compliance mngmt</div>
      <div class="tab" style="width:95px">Maint. Work orders</div>
      <div class="tab" style="width:70px">Work orders</div>
      <div class="tab" style="width:79px">Purchase orders</div>
      <div class="tab" style="width:46px">Files</div>
    </div>

    <article class="info-card">
      <h2>General information</h2>
      <div class="edit-link"><svg width="13" height="12" viewBox="0 0 24 22"><path d="M3 5h9v2H5v12h12v-7h2v9H3z" fill="var(--brand)"/><path d="M19 1l3 3-10 10H9v-3z" fill="var(--brand)"/></svg>Property Edit</div>
      <dl class="fields">
        <div class="field"><dt>Province</dt><dd>Westmark</dd></div>
        <div class="field"><dt>City</dt><dd>Linden Vale</dd></div>
        <div class="field"><dt>Address</dt><dd>100 Harbor Street, Linden Vale</dd></div>
        <div class="field"><dt>GPS Addresse</dt><dd>49.1234567 : -123.4567890000002</dd></div>
        <div class="field"><dt>Postal Code</dt><dd>L4R 2K8</dd></div>
        <div class="field"><dt>Date Build</dt><dd>07/01/1980</dd></div>
        <div class="field"><dt>Area (sq.ft)</dt><dd>1500000.00</dd></div>
        <div class="field"><dt>Lot Size</dt><dd>1500000.00</dd></div>
        <div class="field"><dt>Zoning</dt><dd>CD1</dd></div>
        <div class="field"><dt>Structure type</dt><dd>Steel and concrete</dd></div>
        <div class="field"><dt>Building height</dt><dd>250 mt</dd></div>

        <div class="field"><dt>Clear height</dt><dd>45 mt</dd></div>
        <div class="field"><dt>Floor loading capacity</dt><dd>50</dd></div>
        <div class="field"><dt>Number of floors</dt><dd>30</dd></div>
        <div class="field"><dt>Number of tenants</dt><dd>30</dd></div>
        <div class="field"><dt>Suites</dt><dd>150</dd></div>
        <div class="field"><dt>Typical bay size</dt><dd>-</dd></div>
        <div class="field"><dt>Building envelope</dt><dd>None</dd></div>
        <div class="field"><dt>Parking</dt><dd>Underground + surface</dd></div>
        <div class="field"><dt>Parking ration/N. of stalls</dt><dd>6</dd></div>
        <div class="field"><dt>Sprinkler protected</dt><dd>Yes</dd></div>
        <div class="field"><dt>Sprinkler ESFR</dt><dd>No</dd></div>

        <div class="field"><dt>Sprinkler capacity (gpm)</dt><dd>No</dd></div>
        <div class="field"><dt>Fire alarm panel</dt><dd>Yes</dd></div>
        <div class="field"><dt>Fire alarm monitored</dt><dd>Yes</dd></div>
        <div class="field"><dt>Máximum electrical capacity (Amps)</dt><dd>2500</dd></div>
        <div class="field"><dt>Building back-up power source</dt><dd>Yes</dd></div>
        <div class="field"><dt>Number of elevators</dt><dd>30</dd></div>
        <div class="field"><dt>Number of escalators</dt><dd>5</dd></div>
        <div class="field"><dt>Roof construction</dt><dd>EPDM</dd></div>
        <div class="field"><dt>Roof insulation</dt><dd>-</dd></div>
        <div class="field"><dt>Utility meters</dt><dd>-</dd></div>
        <div class="field"><dt>Aditional information</dt><dd>-</dd></div>
      </dl>
    </article>

    <div class="photo photo--city" role="img" aria-label="Office towers lit at dusk"></div>
    <div class="photo photo--pool" role="img" aria-label="Residential courtyard with swimming pool"></div>
    <div class="photo photo--lounge" role="img" aria-label="Bright apartment living room interior"></div>
    <div class="photo photo--roof" role="img" aria-label="Modern building with cantilevered roof under blue sky"></div>

    <div class="dock">
      <div class="dock-btn dock-btn--home"><svg><use href="#i-home"/></svg></div>
      <div class="dock-btn dock-btn--apps"><svg><use href="#i-grid"/></svg></div>
    </div>
  </section>

</div>
</body>
</html>
```